VFX Company Business Card Design Project

The Kestrel Works is a decentralized Visual Effects Studio servicing the television and feature film industries.
Project Brief:
Take our logo that was previously designed on Pencil Harbor and make a double sided business card.
Requirements:
- Card MUST be double sided.
- Front of card MUST have the yellow part of our logo against the dark grey background.
- Back of card is completely up to the designer.
- Back of card must include the complete company logo.
Please follow these File Preparation guidelines:
http://printnook.ca/infopage?file=filetype_en&s=PrintNook_new&lang=en
Business

```html
<!DOCTYPE html>
<html lang="en">
<head>
<meta charset="utf-8">
<title>The Kestrel Works – Business Cards</title>
<link rel="stylesheet" href="https://fonts.googleapis.com/css2?family=Jost:wght@400;500;600&family=Libre+Baskerville:wght@400;700&display=swap">
<style>
  :root {
    --backdrop: #e6e3de;
    --card-dark: #2b2b2b;
    --brand-yellow: #fdc42c;
    --brand-light: #eef0e6;
    --brand-grey: #5f6a6e;
    --panel-light: #eceee4;
    --ink-dark: #2a2a2a;
    --text-light: #f2f2ee;
  }
  * { box-sizing: border-box; margin: 0; padding: 0; }
  html, body {
    width: 1200px; height: 734px; overflow: hidden;
    background: var(--backdrop);
  }
  .sheet { position: relative; width: 1200px; height: 734px; }
  .card {
    position: absolute;
    width: 524px; height: 300px;
    background: var(--card-dark);
    overflow: hidden;
  }
  .card--front      { left: 66px;  top: 44px; }
  .card--contact    { left: 626px; top: 44px; }
  .card--lockup     { left: 66px;  top: 384px; }
  .card--wordmark   { left: 626px; top: 384px; }

  .brand-name {
    font-family: "Jost", sans-serif;
    font-weight: 600;
    white-space: nowrap;
    letter-spacing: -0.5px;
  }
  .brand-name--yellow { color: var(--brand-yellow); }
  .brand-name--grey   { color: var(--brand-grey); }

  /* Front */
  .card--front .brand-name {
    position: absolute; left: 0; right: 0; top: 112px;
    text-align: center; font-size: 58px;
  }

  /* Contact side */
  .card--contact .brand-name {
    position: absolute; left: 0; right: 0; top: 40px;
    text-align: center; font-size: 56px;
  }
  .address {
    position: absolute; left: 0; right: 0; top: 168px;
    text-align: center;
    font-family: "Libre Baskerville", serif;
    font-size: 13.5px; letter-spacing: 0.6px;
    color: var(--text-light);
  }
  .contact-curve { position: absolute; left: 0; top: 0; }
  .person {
    position: absolute; right: 296px; top: 242px;
    text-align: right;
    font-family: "Libre Baskerville", serif;
    color: var(--ink-dark);
  }
  .person__name  { font-size: 17px; font-weight: 700; }
  .person__title { font-size: 13px; margin-top: 2px; }
  .contact-divider {
    position: absolute; left: 245px; top: 236px;
    width: 1px; height: 58px; background: #9a9e98;
  }
  .contact-list {
    position: absolute; left: 257px; top: 222px;
    list-style: none;
    font-family: "Libre Baskerville", serif;
    font-size: 13px; line-height: 19.5px;
    color: var(--ink-dark);
  }
  .contact-list li { display: flex; align-items: center; gap: 6px; }
  .contact-list svg { width: 11px; height: 11px; fill: var(--ink-dark); }

  /* Lockup side */
  .card--lockup .lockup {
    position: absolute; left: 0; right: 0; top: 104px;
    display: flex; justify-content: center; align-items: center; gap: 14px;
  }
  .lockup__dot {
    width: 40px; height: 40px; border-radius: 50%;
    background: var(--brand-yellow);
  }
  .card--lockup .brand-name { font-size: 44px; }

  .site-url {
    position: absolute; left: 0; right: 0;
    text-align: center;
    font-family: "Jost", sans-serif;
    font-size: 17px; letter-spacing: 2.4px;
    color: var(--text-light);
  }
  .card--lockup .site-url   { top: 252px; }
  .card--wordmark .site-url { top: 256px; }

  /* Wordmark side */
  .card--wordmark .brand-name {
    position: absolute; left: 0; right: 0; top: 108px;
    text-align: center; font-size: 60px;
  }
</style>
</head>
<body>
<main class="sheet">

  <section class="card card--front" aria-label="Card front">
    <div class="brand-name brand-name--yellow">The Kestrel Works</div>
  </section>

  <section class="card card--contact" aria-label="Card back with contact details">
    <div class="brand-name brand-name--grey">The Kestrel Works</div>
    <p class="address">00, Complex name, City, State 0042</p>
    <svg class="contact-curve" width="524" height="300" viewBox="0 0 524 300" aria-hidden="true">
      <path d="M0 246 Q262 170 524 248 L524 300 L0 300 Z" fill="#5f6a6e"/>
      <path d="M0 258 Q262 180 524 258 L524 300 L0 300 Z" fill="var(--panel-light)"/>
    </svg>
    <div class="person">
      <div class="person__name">Your Name</div>
      <div class="person__title">Title</div>
    </div>
    <div class="contact-divider"></div>
    <ul class="contact-list">
      <li><svg viewBox="0 0 12 12"><path d="M2.5 1 L4.5 1 L5.3 3.4 L4 4.4 Q5 6.8 7.6 8 L8.6 6.7 L11 7.5 L11 9.5 Q10.5 11 9 11 Q2 10 1 3 Q1 1.5 2.5 1 Z"/></svg>0987 654321</li>
      <li><svg viewBox="0 0 12 12"><path d="M3 1 H9 Q10 1 10 2 V10 Q10 11 9 11 H3 Q2 11 2 10 V2 Q2 1 3 1 Z M3.5 2.5 V8.5 H8.5 V2.5 Z"/></svg>0987 654321</li>
      <li><svg viewBox="0 0 12 12"><path d="M1 3 H11 V10 H1 Z M1.8 3.6 L6 7 L10.2 3.6" stroke="#eceee4" stroke-width="0.9"/></svg>info@kestrelworks.com</li>
      <li><svg viewBox="0 0 12 12"><circle cx="6" cy="6" r="5"/><path d="M1 6 H11 M6 1 V11 M6 1 Q3 6 6 11 M6 1 Q9 6 6 11" stroke="#eceee4" stroke-width="0.8" fill="none"/></svg>www.kestrelworks.com</li>
    </ul>
  </section>

  <section class="card card--lockup" aria-label="Card back with logo">
    <div class="lockup">
      <span class="lockup__dot"></span>
      <span class="brand-name brand-name--grey">The Kestrel Works</span>
    </div>
    <p class="site-url">www.kestrelworks.com</p>
  </section>

  <section class="card card--wordmark" aria-label="Card back with name">
    <div class="brand-name brand-name--grey">The Kestrel Works</div>
    <p class="site-url">www.kestrelworks.com</p>
  </section>

</main>
</body>
</html>
```